NEW Modern Sleek Business Card for VR Language Startup

Our startup is using VR to lead the next wave of world language education. We need a two-sided business card that introduces the larger organization (Brightloom Language Inc) and our contact info on one side and shows the product, Glimwoorld, on the other side.

Side 1 (contact info)= Brightloom Logo and Contact info (name, title, phone, email)

Side 2 (product)= Glimworld logo, text, and website
Text= Culturally Immersive Language Learning Games
Website= www.glimworld-play.com

Target Market(s)

Education, Technology

Contact Information for Business Card

Contact info will be updated upon approval of the design. For now, put this as a placeholder.

Perry Dunmore
Founder & CEO
pdunmore@quillpost-mail.net
(555)-014-2286

Font styles to use
Other font styles liked:
• Gibson and Century Gothic are the brand fonts

Requirements
Nice to have
• I would love to see cohesion between the design and colors of the two logos. I have attached a few business card designs that I like, so you can get a feel for my preferred style.

```html
<!DOCTYPE html>
<html lang="en">
<head>
<meta charset="utf-8">
<title>Brightloom Language – Glimworld Business Card</title>
<link rel="stylesheet" href="https://fonts.googleapis.com/css2?family=Montserrat:wght@500;600;700&family=Questrial&display=swap">
<style>
  :root {
    --stage: #1c1c1f;
    --card-black: #050507;
    --white: #ffffff;
    --cyan: #3fc6e6;
    --violet: #6a5bb8;
    --pink: #e8336d;
    --magenta: #c43c8f;
    --purple: #7b4fc0;
    --text-soft: #e9e9ee;
    --rule: #8a4fb8;
  }
  * { box-sizing: border-box; margin: 0; padding: 0; }
  html, body {
    width: 1200px; height: 800px; overflow: hidden;
    background: var(--stage);
    font-family: "Questrial", "Century Gothic", sans-serif;
  }
  .sheet {
    width: 1200px; height: 800px;
    display: flex; align-items: center; justify-content: center; gap: 40px;
  }

  /* ---------- Product side ---------- */
  .product-card {
    width: 540px; height: 310px; padding: 12px;
    border-radius: 26px;
    background: linear-gradient(135deg, var(--cyan), var(--violet));
  }
  .product-card__face {
    width: 100%; height: 100%;
    border-radius: 18px;
    background: var(--card-black);
    display: flex; flex-direction: column; align-items: center; justify-content: center;
    color: var(--white);
  }
  .product-logo { display: flex; align-items: center; gap: 14px; }
  .product-logo__dot {
    width: 30px; height: 30px; border-radius: 50%;
    background: var(--cyan);
  }
  .product-logo__name {
    font-family: "Montserrat", sans-serif; font-weight: 600;
    font-size: 46px; letter-spacing: 0.5px; color: var(--white);
  }
  .product-tagline {
    margin-top: 18px;
    font-family: "Montserrat", sans-serif; font-weight: 500;
    font-size: 17px; color: var(--text-soft);
  }
  .product-url {
    margin-top: 6px;
    font-family: "Montserrat", sans-serif; font-weight: 500;
    font-size: 16px; color: var(--text-soft);
  }
  .product-url__brand { color: var(--cyan); }

  /* ---------- Contact side ---------- */
  .contact-card {
    position: relative;
    width: 540px; height: 310px;
    border-radius: 24px; overflow: hidden;
    background: var(--card-black);
  }
  .brand-panel {
    position: absolute; left: 0; top: 34px; bottom: 0; width: 262px;
    background: linear-gradient(160deg, var(--pink), var(--magenta) 55%, var(--purple));
    border-top-right-radius: 46px;
  }
  .brand-panel__fill {
    position: absolute; left: 0; top: 8px; right: 8px; bottom: 0;
    background: var(--white);
    border-top-right-radius: 38px;
    display: flex; align-items: center; justify-content: center;
  }
  .brand-logo { display: flex; align-items: center; gap: 10px; }
  .brand-logo__dot {
    width: 24px; height: 24px; border-radius: 50%;
    background: var(--pink);
  }
  .brand-logo__name {
    font-family: "Montserrat", sans-serif; font-weight: 700;
    font-size: 28px; letter-spacing: 1px; color: #1a1a1a;
  }

  .contact-info {
    position: absolute; left: 262px; right: 0; top: 0; bottom: 0;
    display: flex; flex-direction: column; align-items: center; justify-content: center;
    color: var(--white); text-align: center;
  }
  .contact-info__name {
    font-family: "Montserrat", sans-serif; font-weight: 600;
    font-size: 20px; letter-spacing: 0.5px; text-transform: uppercase;
  }
  .contact-info__title {
    font-family: "Montserrat", sans-serif; font-weight: 600;
    font-size: 14px; margin-top: 2px;
    background: linear-gradient(90deg, var(--violet), var(--pink));
    -webkit-background-clip: text; background-clip: text; color: transparent;
  }
  .contact-info__rule {
    width: 210px; height: 1px; margin: 14px 0 12px;
    background: linear-gradient(90deg, transparent, var(--rule), transparent);
  }
  .contact-line { display: flex; flex-direction: column; align-items: center; margin-bottom: 10px; }
  .contact-icon { width: 24px; height: 24px; margin-bottom: 4px; }
  .contact-line__text {
    font-family: "Montserrat", sans-serif; font-weight: 500; font-size: 13px;
  }
  .contact-info__web {
    margin-top: 6px;
    font-family: "Montserrat", sans-serif; font-weight: 500; font-size: 13px;
  }
  .contact-info__web-brand { color: var(--cyan); }
</style>
</head>
<body>
<main class="sheet">

  <section class="product-card" aria-label="Glimworld product side">
    <div class="product-card__face">
      <div class="product-logo">
        <span class="product-logo__dot"></span>
        <span class="product-logo__name">Glimworld</span>
      </div>
      <p class="product-tagline">Culturally Immersive Language Learning Games</p>
      <p class="product-url">www.<span class="product-url__brand">glimworld</span>-play.com</p>
    </div>
  </section>

  <section class="contact-card" aria-label="Brightloom Language contact side">
    <div class="brand-panel">
      <div class="brand-panel__fill">
        <div class="brand-logo">
          <span class="brand-logo__dot"></span>
          <span class="brand-logo__name">Brightloom</span>
        </div>
      </div>
    </div>

    <div class="contact-info">
      <h1 class="contact-info__name">Perry Dunmore</h1>
      <p class="contact-info__title">Founder &amp; CEO</p>
      <div class="contact-info__rule"></div>

      <div class="contact-line">
        <svg class="contact-icon" viewBox="0 0 24 24" aria-hidden="true">
          <defs>
            <linearGradient id="icon-ring" x1="0" y1="0" x2="1" y2="1">
              <stop offset="0" stop-color="#e8336d"/>
              <stop offset="1" stop-color="#3fc6e6"/>
            </linearGradient>
          </defs>
          <circle cx="12" cy="12" r="11" fill="url(#icon-ring)"/>
          <circle cx="12" cy="12" r="8" fill="#ffffff"/>
          <path d="M9.2 7.5l1.4 0.3 0.7 2-1 0.9a6 6 0 0 0 2.9 2.9l0.9-1 2 0.7 0.3 1.4-1.2 1.1c-3.2-0.3-6.4-3.5-6.7-6.7z" fill="#1a1a1a"/>
        </svg>
        <span class="contact-line__text">(555)-014-2286</span>
      </div>

      <div class="contact-line">
        <svg class="contact-icon" viewBox="0 0 24 24" aria-hidden="true">
          <circle cx="12" cy="12" r="11" fill="url(#icon-ring)"/>
          <circle cx="12" cy="12" r="8" fill="#ffffff"/>
          <rect x="7.5" y="9" width="9" height="6.5" rx="0.8" fill="none" stroke="#1a1a1a" stroke-width="1.3"/>
          <path d="M7.8 9.4l4.2 3.2 4.2-3.2" fill="none" stroke="#1a1a1a" stroke-width="1.3"/>
        </svg>
        <span class="contact-line__text">pdunmore@quillpost-mail.net</span>
      </div>

      <p class="contact-info__web">www.<span class="contact-info__web-brand">glimworld</span>-play.com</p>
    </div>
  </section>

</main>
</body>
</html>
```